Meridale Staffing Website

My business has been word of mouth over the last 3 years and has grown. Now I need a website for additional marketing as we have new clients asking for a website.

You have already completed my Logo during an earlier project. I have attached the logo.

We do Staff Augmentation and Operation Support.

What is that?
Staff augmentation is an outsourcing strategy that allows companies to fill specific, temporary roles to achieve business objectives. This staffing method complements existing teams with specific talent, enhancing business capabilities or filling gaps left by members on extended leave.

We work alongside the internal recruiting team to assist clients to meet and exceed financial goals.

```html
<!DOCTYPE html>
<html lang="en">
<head>
<meta charset="utf-8">
<title>Meridale Staffing</title>
<link href="https://fonts.googleapis.com/css2?family=Montserrat:wght@500;600;700;800&family=Open+Sans:wght@400;600&display=swap" rel="stylesheet">
<style>
:root{
  --navy:#0f3d6b;
  --navy-dark:#0a2b4e;
  --ink:#1b1b1b;
  --text:#444;
  --grey-bg:#f4f4f4;
  --line:#bdbdbd;
  --white:#fff;
  --black:#050505;
}
*{box-sizing:border-box;margin:0;padding:0}
html,body{width:1200px;height:4640px;overflow:hidden;background:var(--white)}
body{position:relative;font-family:'Open Sans',sans-serif;color:var(--text)}
.abs{position:absolute}
h1,h2,h3,.heading{font-family:'Montserrat',sans-serif}

/* top bar */
.top-bar{left:0;top:0;width:1200px;height:31px;background:var(--navy-dark);color:#fff;font-size:12px;text-align:center;line-height:31px;font-family:'Montserrat',sans-serif;font-weight:500}

/* header */
.site-header{left:0;top:31px;width:1200px;height:99px;background:#fff}
.brand{display:flex;align-items:center;gap:10px}
.brand-dot{width:46px;height:46px;border-radius:50%;background:var(--navy);flex:none}
.brand-name{font-family:'Montserrat',sans-serif;font-weight:700;color:var(--navy);font-size:22px;line-height:1.05;white-space:nowrap}
.main-nav{left:326px;top:80px;display:flex;gap:26px;font-family:'Montserrat',sans-serif;font-weight:700;font-size:12.5px;color:#222}
.main-nav .active{color:var(--navy)}
.call{left:864px;top:62px;display:flex;align-items:center;gap:14px}
.call-icon{width:50px;height:50px;border-radius:50%;background:var(--navy);display:flex;align-items:center;justify-content:center}
.call small{display:block;font-size:12px;color:#333;font-family:'Montserrat',sans-serif;font-weight:500}
.call strong{display:block;font-size:22px;color:var(--navy);font-family:'Montserrat',sans-serif;font-weight:700;line-height:1.1}

/* hero */
.hero{left:0;top:130px;width:1200px;height:645px;background:linear-gradient(180deg,#5c6167 0%,#75797e 45%,#8c9095 100%)}
.hero h1{position:absolute;left:0;width:1200px;top:138px;text-align:center;color:#fff;font-size:50px;font-weight:700;line-height:52px;letter-spacing:.5px}
.hero p{position:absolute;left:0;width:1200px;top:253px;text-align:center;color:#fff;font-size:15px;line-height:31px}
.hero svg{position:absolute;left:0;top:0}

/* section titles */
.section-title{width:1200px;left:0;text-align:center;font-family:'Montserrat',sans-serif;font-weight:700;font-size:34px;color:#1a1a1a}
.title-bar{width:40px;height:4px;background:var(--navy);left:580px}

/* services */
.service-card{top:928px;width:315px;height:304px;background:#fff;border-radius:8px;box-shadow:0 4px 14px rgba(0,0,0,.18);text-align:center;padding-top:20px}
.service-card.featured{background:var(--navy);color:#fff}
.service-card h3{font-size:16px;font-weight:700;color:var(--navy);margin-top:14px;letter-spacing:.2px}
.service-card.featured h3{color:#fff}
.service-card p{font-size:12.5px;line-height:26px;margin:10px 36px 0}
.service-card a{display:inline-block;margin-top:14px;font-family:'Montserrat',sans-serif;font-weight:700;font-size:13px;color:var(--navy);text-decoration:underline}
.service-card.featured a{color:#fff}
.arrow-btn{width:46px;height:46px;border-radius:50%;background:var(--navy);top:1006px;display:flex;align-items:center;justify-content:center;z-index:2}

/* about */
.about{left:0;top:1324px;width:1200px;height:680px;background:var(--grey-bg)}
.about-photo{left:72px;top:1333px;width:468px;height:631px;background:radial-gradient(circle at 45% 40%,#d8d2cb 0%,#8b7f78 40%,#2b3a4f 75%,#f4f4f4 76%)}
.about h2{position:absolute;left:584px;top:92px;font-size:33px;font-weight:700;color:#1a1a1a}
.about p{position:absolute;left:584px;top:164px;width:504px;font-size:13.5px;line-height:25.8px;text-align:justify}
.pill-btn{display:flex;align-items:center;gap:12px;background:var(--navy);color:#fff;border-radius:26px;font-family:'Montserrat',sans-serif;font-weight:700;font-size:15px;padding:0 18px 0 4px}
.pill-btn .dot{width:42px;height:42px;border-radius:50%;background:#fff;border:3px solid var(--navy);box-shadow:0 0 0 2px #fff inset}

/* benefits */
.benefits{left:0;top:1928px;width:1200px;height:880px}
.benefit-label{font-family:'Montserrat',sans-serif;font-weight:700;font-size:15.5px;color:#fff;white-space:nowrap}
.benefit-label.right{text-align:right}

/* blogs */
.blog-card{width:476px;height:198px;background:#fff;box-shadow:0 3px 10px rgba(0,0,0,.18)}
.blog-img{position:absolute;left:0;top:0;width:191px;height:198px}
.blog-body{position:absolute;left:207px;top:18px;width:258px}
.blog-body h3{font-size:16.5px;font-weight:700;color:var(--navy)}
.blog-body time{display:block;font-size:12px;color:#222;margin-top:8px;font-weight:600}
.blog-body p{font-size:11.5px;line-height:24px;margin-top:8px}
.blog-meta{display:flex;justify-content:space-between;width:215px;margin-top:6px;font-family:'Montserrat',sans-serif;font-weight:700;font-size:12px;color:var(--navy)}
.blog-meta span{color:#888;font-size:10px;font-weight:600}

/* contact */
.contact{left:0;top:3496px;width:1200px;height:620px;background:linear-gradient(180deg,#f6f5f3 0%,#ecebe8 60%,#f4f3f1 100%)}
.field{background:#fff;border:1.5px solid #9a9a9a;border-radius:4px;font-size:12.5px;color:#333;padding:14px 18px}

/* footer */
.footer{left:0;top:4020px;width:1200px;height:620px}
.mail-title{left:0;width:1200px;top:4153px;text-align:center;color:#fff;font-family:'Montserrat',sans-serif;font-weight:700;font-size:33px}
.mail-sub{left:0;width:1200px;top:4211px;text-align:center;color:#fff;font-size:13px}
.mail-form{left:276px;top:4253px;width:641px;height:50px;background:#fff;border-radius:26px}
.mail-form span{position:absolute;left:46px;top:16px;font-size:12px;color:#aaa}
.mail-form b{position:absolute;right:3px;top:3px;width:148px;height:44px;border-radius:22px;background:var(--navy);color:#fff;font-family:'Montserrat',sans-serif;font-size:16px;text-align:center;line-height:44px;font-weight:700}
.foot-rule{left:88px;width:1024px;height:1px;background:#444}
.foot-col h4{font-family:'Montserrat',sans-serif;font-weight:700;color:#fff;font-size:16px;margin-bottom:10px}
.foot-col li{list-style:none;color:#fff;font-size:13.5px;line-height:30px}
.foot-col li::before{content:"»";margin-right:10px}
.foot-col.contact-info li::before{content:none}
.foot-col.contact-info li{display:flex;gap:12px;align-items:flex-start;line-height:27px}
.social{left:126px;top:4503px;display:flex;gap:18px}
.social i{display:block;width:30px;height:30px;border-radius:50%;background:var(--navy)}
.copyright{left:0;width:1200px;top:4588px;text-align:center;color:#fff;font-size:12px}
</style>
</head>
<body>

<div class="abs top-bar">Lorem ipsum dolor sit amet, consectetur adipiscing elit, sed do eiusmod tempor incididunt ut l</div>

<header class="abs site-header">
  <div class="abs brand" style="left:90px;top:26px">
    <span class="brand-dot"></span>
    <span class="brand-name">Meridale<br>Staffing</span>
  </div>
</header>
<nav class="abs main-nav">
  <span class="active">HOME</span><span>ABOUT US</span><span>SERVICES</span><span>REVIEWS</span><span>BLOGS</span><span>CONTACT US</span>
</nav>
<div class="abs call">
  <span class="call-icon"><svg width="22" height="22" viewBox="0 0 24 24" fill="none" stroke="#fff" stroke-width="1.8"><path d="M5 3h4l2 5-2.5 1.5a11 11 0 0 0 6 6L16 13l5 2v4a2 2 0 0 1-2 2A17 17 0 0 1 3 5a2 2 0 0 1 2-2z"/></svg></span>
  <div><small>Call Us Today</small><strong>+1 888 888 8888</strong></div>
</div>

<section class="abs hero">
  <div class="abs" role="img" aria-label="Photo of business people walking through a busy city crowd" style="left:0;top:0;width:1200px;height:645px"></div>
  <h1>STAFF AUGMENTATION<br>IS AN OUTSOURCING STRATEGY</h1>
  <p>Lorem ipsum dolor sit amet, consectetur adipiscing elit, sed do eiusmod tempor incididunt ut labore et dolore magna aliqua.<br>Ut enim ad minim veniam, quis nostrud exercitation ullamco laboris.</p>
  <svg width="1200" height="645" viewBox="0 0 1200 645">
    <circle cx="600" cy="420" r="76" fill="#fff" fill-opacity=".25"/>
    <circle cx="600" cy="420" r="43" fill="#1a4f86"/>
    <path d="M591 405 L614 420 L591 435 Z" fill="#fff"/>
    <path d="M0 480 Q600 768 1200 480" fill="none" stroke="var(--navy)" stroke-width="8"/>
    <path d="M0 492 Q600 780 1200 492 L1200 645 L0 645 Z" fill="#fff"/>
  </svg>
</section>

<h2 class="abs section-title" style="top:846px">OUR SERVICES</h2>
<div class="abs title-bar" style="top:892px"></div>

<div class="abs arrow-btn" style="left:71px"><svg width="12" height="12" viewBox="0 0 12 12"><path d="M8 1 L3 6 L8 11" fill="none" stroke="#fff" stroke-width="2.2"/></svg></div>
<div class="abs arrow-btn" style="left:1082px"><svg width="12" height="12" viewBox="0 0 12 12"><path d="M4 1 L9 6 L4 11" fill="none" stroke="#fff" stroke-width="2.2"/></svg></div>

<article class="abs service-card" style="left:99px">
  <svg width="80" height="80" viewBox="0 0 80 80" fill="none" stroke="var(--navy)" stroke-width="2.5"><rect x="26" y="6" width="28" height="66" rx="4"/><path d="M40 26 L52 33 L52 47 L40 54 L28 47 L28 33 Z"/><path d="M28 33 L40 40 L52 33 M40 40 V54"/><path d="M14 40 L26 30 M14 40 L26 50 M66 40 L54 30 M66 40 L54 50"/></svg>
  <h3>STAFF AUGMENTATION</h3>
  <p>Lorem ipsum dolor sit amet, consectetur adipiscing elit, sed do eiusmod tempor incididunt ut labore et dolore.</p>
  <a>LEARN MORE</a>
</article>
<article class="abs service-card featured" style="left:443px">
  <svg width="80" height="80" viewBox="0 0 80 80" fill="none" stroke="#fff" stroke-width="2.5"><circle cx="40" cy="28" r="18"/><circle cx="40" cy="24" r="6"/><path d="M30 38 a10 10 0 0 1 20 0"/><path d="M8 60 L22 48 L34 56 M72 60 L58 48 L46 56 M34 56 L40 62 L46 56"/></svg>
  <h3>OPERATION SUPPORT</h3>
  <p>Lorem ipsum dolor sit amet, consectetur adipiscing elit, sed do eiusmod tempor incididunt ut labore et dolore.</p>
  <a>LEARN MORE</a>
</article>
<article class="abs service-card" style="left:787px">
  <svg width="80" height="80" viewBox="0 0 80 80" fill="none" stroke="var(--navy)" stroke-width="2.5"><path d="M16 6 H46 L56 16 V70 H16 Z"/><rect x="22" y="22" width="8" height="8"/><rect x="22" y="38" width="8" height="8"/><path d="M34 26 H46 M34 42 H40"/><circle cx="54" cy="50" r="12"/><path d="M48 50 L52 54 L60 46 M63 59 L72 68"/></svg>
  <h3>BACKGROUND VERIFICATION</h3>
  <p>Lorem ipsum dolor sit amet, consectetur adipiscing elit, sed do eiusmod tempor incididunt ut labore et dolore.</p>
  <a>LEARN MORE</a>
</article>

<section class="abs about">
  <h2>ABOUT MERIDALE STAFFING</h2>
  <p>Lorem ipsum dolor sit amet, consectetur adipiscing elit, sed do eiusmod tempor incididunt ut labore et dolore magna aliqua. Quis ipsum suspendisse ultrices gravida. Risus commodo viverra maecenas accumsan lacus vel facilisis. Lorem ipsum dolor sit amet, consectetur adipiscing elit, sed do eiusmod tempor incididunt ut labore et dolore magna aliqua. Ut enim ad minim veniam, quis nostrud exercitation ullamco laboris nisi ut aliquip ex ea commodo consequat. Duis aute irure dolor in reprehenderit in voluptate velit esse cillum dolore eu fugiat nulla pariatur. Excepteur sint occaecat cupidatat non proident, sunt in culpa qui officia deserunt mollit anim id est laborum.Duis aute irure dolor in reprehenderit in voluptate velit esse cillum dolore eu fugiat nulla pariatur.</p>
  <div class="abs pill-btn" style="left:584px;top:465px;height:51px"><span class="dot"></span>LEARN MORE</div>
</section>
<div class="abs about-photo" role="img" aria-label="Portrait of a smiling businessman in a dark blazer with arms crossed, framed by navy and grey circular rings"></div>

<section class="abs benefits">
  <svg class="abs" style="left:0;top:0" width="1200" height="880" viewBox="0 0 1200 880">
    <path d="M0 57 Q600 -63 1200 57" fill="none" stroke="#666" stroke-width="9"/>
    <path d="M0 63 Q600 -57 1200 63 L1200 802 Q600 946 0 802 Z" fill="var(--navy)"/>
    <path d="M0 808 Q600 952 1200 808" fill="none" stroke="#666" stroke-width="9"/>
    <circle cx="586" cy="474" r="231" fill="none" stroke="#fff" stroke-width="1.5"/>
    <circle cx="586" cy="474" r="170" fill="none" stroke="#fff" stroke-width="1.5" stroke-dasharray="5 5"/>
    <circle cx="586" cy="474" r="126" fill="#fff"/>
    <text x="586" y="468" text-anchor="middle" font-family="Montserrat, sans-serif" font-weight="700" font-size="22" fill="#0f3d6b">Meridale</text>
    <text x="586" y="496" text-anchor="middle" font-family="Montserrat, sans-serif" font-weight="700" font-size="22" fill="#0f3d6b">Staffing</text>
    <g fill="#fff" stroke="#0f3d6b" stroke-width="2">
      <circle cx="595" cy="247" r="36"/><circle cx="413" cy="325" r="36"/><circle cx="748" cy="325" r="36"/>
      <circle cx="357" cy="483" r="36"/><circle cx="818" cy="483" r="36"/>
      <circle cx="422" cy="649" r="36"/><circle cx="746" cy="649" r="36"/><circle cx="577" cy="712" r="36"/>
    </g>
    <g fill="none" stroke="#0f3d6b" stroke-width="2">
      <circle cx="595" cy="247" r="16"/><path d="M595 237 V247 L602 252"/>
      <path d="M404 316 V336 M413 312 V336 M422 320 V336"/>
      <circle cx="748" cy="320" r="10"/><path d="M734 338 H762"/>
      <circle cx="357" cy="483" r="15"/><circle cx="357" cy="483" r="6"/>
      <path d="M808 473 V493 L803 488 M818 473 V493 L813 488 M828 473 V493 L823 488"/>
      <rect x="410" y="640" width="24" height="20"/><path d="M410 648 H434"/>
      <circle cx="746" cy="649" r="15"/><path d="M738 649 L744 655 L755 643"/>
      <circle cx="577" cy="712" r="16"/><path d="M577 702 V712 L584 717"/>
    </g>
  </svg>
  <h2 class="abs section-title" style="top:76px;color:#fff">OUR BENEFITS</h2>
  <div class="abs title-bar" style="top:122px;background:#fff"></div>
  <span class="abs benefit-label" style="left:517px;top:178px">LOREM IPSUM DOLOR</span>
  <span class="abs benefit-label right" style="left:146px;width:200px;top:315px">LOREM IPSUM DOLOR</span>
  <span class="abs benefit-label" style="left:800px;top:315px">LOREM IPSUM DOLOR</span>
  <span class="abs benefit-label right" style="left:115px;width:200px;top:473px">LOREM IPSUM DOLOR</span>
  <span class="abs benefit-label" style="left:870px;top:473px">LOREM IPSUM DOLOR</span>
  <span class="abs benefit-label right" style="left:160px;width:200px;top:639px">LOREM IPSUM DOLOR</span>
  <span class="abs benefit-label" style="left:800px;top:639px">LOREM IPSUM DOLOR</span>
  <span class="abs benefit-label" style="left:500px;top:776px">LOREM IPSUM DOLOR</span>
</section>

<h2 class="abs section-title" style="top:2880px">OUR LATEST BLOGS</h2>
<div class="abs title-bar" style="top:2930px"></div>

<article class="abs blog-card" style="left:112px;top:2977px">
  <div class="blog-img" role="img" aria-label="Photo of a team stacking hands together in an office" style="background:linear-gradient(135deg,#c9b8a6,#7d6a5e)"></div>
  <div class="blog-body"><h3>LOREM IPSUM DOLOR SIT</h3><time>JAN 11 2021</time><p>Lorem ipsum dolor sit amet, consectetur adipiscing elit, sed do eiusmod tempor incididunt ut labore et.</p><div class="blog-meta">LEARN MORE<span>15 COMMENT</span></div></div>
</article>
<article class="abs blog-card" style="left:614px;top:2977px">
  <div class="blog-img" role="img" aria-label="Photo of a cheering group of colleagues in a bright office" style="background:linear-gradient(135deg,#d4d6d8,#6b7580)"></div>
  <div class="blog-body"><h3>LOREM IPSUM DOLOR SIT</h3><time>JAN 11 2021</time><p>Lorem ipsum dolor sit amet, consectetur adipiscing elit, sed do eiusmod tempor incididunt ut labore et.</p><div class="blog-meta">LEARN MORE<span>15 COMMENT</span></div></div>
</article>
<article class="abs blog-card" style="left:112px;top:3208px">
  <div class="blog-img" role="img" aria-label="Photo of a smiling businessman in a grey suit with coworkers behind" style="background:linear-gradient(135deg,#d9d9d9,#5e6268)"></div>
  <div class="blog-body"><h3>LOREM IPSUM DOLOR SIT</h3><time>JAN 11 2021</time><p>Lorem ipsum dolor sit amet, consectetur adipiscing elit, sed do eiusmod tempor incididunt ut labore et.</p><div class="blog-meta">LEARN MORE<span>15 COMMENT</span></div></div>
</article>
<article class="abs blog-card" style="left:614px;top:3208px">
  <div class="blog-img" role="img" aria-label="Photo of two colleagues talking at a desk by a window" style="background:linear-gradient(135deg,#e3e3e0,#8a857d)"></div>
  <div class="blog-body"><h3>LOREM IPSUM DOLOR SIT</h3><time>JAN 11 2021</time><p>Lorem ipsum dolor sit amet, consectetur adipiscing elit, sed do eiusmod tempor incididunt ut labore et.</p><div class="blog-meta">LEARN MORE<span>15 COMMENT</span></div></div>
</article>

<section class="abs contact" role="img" aria-label="Faded photo of an office team in the background"></section>
<h2 class="abs section-title" style="top:3553px">GET IN TOUCH</h2>
<div class="abs title-bar" style="top:3601px"></div>
<div class="abs field" style="left:202px;top:3640px;width:393px;height:45px">First name</div>
<div class="abs field" style="left:605px;top:3640px;width:393px;height:45px">Last name</div>
<div class="abs field" style="left:202px;top:3700px;width:393px;height:45px">Email</div>
<div class="abs field" style="left:605px;top:3700px;width:393px;height:45px">Phone</div>
<div class="abs field" style="left:202px;top:3759px;width:796px;height:114px">Message</div>
<div class="abs pill-btn" style="left:503px;top:3901px;width:194px;height:51px;gap:30px">
  <span class="dot"></span>SUBMIT</div>

<footer class="abs footer">
  <svg class="abs" style="left:0;top:0" width="1200" height="620" viewBox="0 0 1200 620">
    <path d="M0 131 Q600 -141 1200 131" fill="none" stroke="var(--navy)" stroke-width="9"/>
    <path d="M0 143 Q600 -129 1200 143 L1200 620 L0 620 Z" fill="var(--black)"/>
  </svg>
</footer>
<h2 class="abs mail-title">JOIN OUR MAILING LIST</h2>
<p class="abs mail-sub">Lorem ipsum dolor sit amet, consectetur adipiscing elit, sed do eiusmod tempor</p>
<div class="abs mail-form"><span>Enter Email Here</span><b>SUBSCRIBE</b></div>
<div class="abs foot-rule" style="top:4343px"></div>

<div class="abs brand" style="left:112px;top:4416px">
  <span class="brand-dot" style="background:#fff"></span>
  <span class="brand-name" style="color:#fff">Meridale<br>Staffing</span>
</div>
<div class="abs social" aria-label="Social links"><i></i><i></i><i></i><i></i></div>

<div class="abs foot-col" style="left:391px;top:4376px"><h4>QUICK LINKS</h4>
  <ul><li>Home</li><li>About Us</li><li>Services</li><li>Reviews</li><li>Blog</li></ul></div>
<div class="abs foot-col" style="left:645px;top:4376px"><h4>LEGAL</h4>
  <ul><li>Terms of Use</li><li>Privacy Policy</li><li>Contact Us</li><li>Sitmap</li></ul></div>
<div class="abs foot-col contact-info" style="left:863px;top:4376px"><h4>CONTACT US</h4>
  <ul>
    <li><svg width="12" height="16" viewBox="0 0 12 16" style="margin-top:5px;flex:none"><path d="M6 0a6 6 0 0 1 6 6c0 4-6 10-6 10S0 10 0 6a6 6 0 0 1 6-6z" fill="#fff"/><circle cx="6" cy="6" r="2" fill="#000"/></svg><span>123 Lorem ipsum dolor sit amet<br>consectetur adipiscing.</span></li>
    <li><svg width="13" height="13" viewBox="0 0 24 24" style="margin-top:7px;flex:none"><path d="M5 3h4l2 5-2.5 1.5a11 11 0 0 0 6 6L16 13l5 2v4a2 2 0 0 1-2 2A17 17 0 0 1 3 5a2 2 0 0 1 2-2z" fill="#fff"/></svg><span>+1 888 888 8888</span></li>
    <li style="margin-top:14px"><svg width="15" height="11" viewBox="0 0 15 11" style="margin-top:9px;flex:none"><rect width="15" height="11" fill="#fff"/><path d="M0 0 L7.5 6 L15 0" fill="none" stroke="#000"/></svg><span>hello@meridalestaffing.com</span></li>
  </ul></div>

<div class="abs foot-rule" style="top:4572px"></div>
<p class="abs copyright">© Copyrights 2022 Meridale Staffing &nbsp;|&nbsp;&nbsp; All Rights Reserved</p>

</body>
</html>
```